Velk Partners Building Business Cards

We need a business card that reflects our business as "Solar Experts" in San Diego. Browse our website www.velkpartners.example our License needs to be displayed as "CSLB# 3867140" our phone number is (619) 555-0187

Save thousands on your electric bills and increase the value of your home while helping to protect the environment. Our solar installation experts will help you design the system that's right for you, using only the highest quality equipment that will look great and give you ideal performance. Our goal is to make you energy independent, and get your electric bill to 0.

Paul Osterby
(619) 555-0187
paul@velkpartners.example

Target Market(s)

Home owners in san diego looking for solar

Industry/Entity Type

Solar Energy

Contact Information for Business Card

Paul Osterby
(619) 555-0187
paul@velkpartners.example

Font styles to use
Other font styles liked:
• Use our logo font

Requirements
Must have
• License needs to be displayed as "CSLB# 3867140" our phone number is (619) 555-0187
Nice to have
• Real images of rooftop home solar in san diego
Should not have
• our business address

```html
<!DOCTYPE html>
<html lang="en">
<head>
<meta charset="utf-8">
<title>Velk Partners Building – Business Cards</title>
<link rel="stylesheet" href="https://fonts.googleapis.com/css2?family=Open+Sans:wght@400;600;700;800&display=swap">
<style>
  :root {
    --navy: #1f3f7a;
    --gold: #f2a900;
    --white: #ffffff;
    --paper: #ffffff;
    --backdrop: #e9e7e3;
    --photo-top: #3a5488;
    --photo-bottom: #2a3f6c;
    --card-w: 560px;
    --card-h: 320px;
  }
  * { box-sizing: border-box; margin: 0; padding: 0; }
  html, body {
    width: 1200px; height: 900px; overflow: hidden;
    background: var(--backdrop);
    font-family: "Open Sans", Arial, sans-serif;
  }
  .canvas { position: relative; width: 1200px; height: 900px; }
  .card {
    position: absolute;
    width: var(--card-w); height: var(--card-h);
    overflow: hidden;
    box-shadow: 0 6px 18px rgba(0,0,0,0.18);
    background: var(--paper);
  }
  .card--front { left: 80px; top: 110px; }
  .card--back { left: 560px; top: 470px; }

  /* front */
  .rooftop-photo {
    position: absolute; inset: 0;
    background: linear-gradient(180deg, var(--photo-top) 0%, var(--photo-bottom) 100%);
  }
  .front-brand {
    position: absolute; left: 0; right: 0; top: 0; bottom: 0;
    display: flex; align-items: center; justify-content: center; gap: 14px;
  }
  .brand-dot { width: 22px; height: 22px; border-radius: 50%; background: var(--white); flex: none; }
  .brand-name {
    font-weight: 800; font-size: 38px; letter-spacing: -0.5px;
    color: var(--white); white-space: nowrap;
  }

  /* back */
  .back-top {
    position: absolute; left: 0; top: 0; right: 0; height: 178px;
    display: flex; align-items: center; justify-content: center; gap: 12px;
  }
  .back-top .brand-dot { background: var(--navy); }
  .back-top .brand-name { color: var(--navy); }
  .gold-rule { position: absolute; left: 0; right: 0; top: 178px; height: 6px; background: var(--gold); }
  .back-band {
    position: absolute; left: 0; right: 0; top: 184px; bottom: 0;
    background: var(--navy); color: var(--white);
    display: flex; align-items: center; justify-content: center;
  }
  .person { text-align: right; padding-right: 18px; border-right: 1px solid rgba(255,255,255,0.6); }
  .person-name { font-weight: 700; font-size: 17px; letter-spacing: 0.5px; text-transform: uppercase; }
  .person-license { font-size: 15px; margin-top: 4px; }
  .person-license strong { font-weight: 700; }
  .contacts { list-style: none; padding-left: 16px; font-size: 14px; }
  .contacts li { display: flex; align-items: center; gap: 8px; line-height: 1.7; }
  .contacts svg { width: 13px; height: 13px; fill: var(--white); }
</style>
</head>
<body>
<main class="canvas">
  <section class="card card--front">
    <div class="rooftop-photo" role="img" aria-label="Photo of rooftop solar panels on a tile-roofed home"></div>
    <div class="front-brand">
      <span class="brand-dot"></span>
      <span class="brand-name">Velk Partners Building</span>
    </div>
  </section>

  <section class="card card--back">
    <div class="back-top">
      <span class="brand-dot"></span>
      <span class="brand-name">Velk Partners Building</span>
    </div>
    <div class="gold-rule"></div>
    <div class="back-band">
      <div class="person">
        <p class="person-name">Paul Osterby</p>
        <p class="person-license"><strong>License:</strong> CSLB# 3867140</p>
      </div>
      <ul class="contacts">
        <li>
          <svg viewBox="0 0 24 24" aria-hidden="true"><path d="M6.6 10.8a15.1 15.1 0 0 0 6.6 6.6l2.2-2.2a1 1 0 0 1 1-.25 11.4 11.4 0 0 0 3.6.57 1 1 0 0 1 1 1V20a1 1 0 0 1-1 1A17 17 0 0 1 3 4a1 1 0 0 1 1-1h3.5a1 1 0 0 1 1 1c0 1.25.2 2.45.57 3.57a1 1 0 0 1-.25 1z"/></svg>
          (619) 555-0187
        </li>
        <li>
          <svg viewBox="0 0 24 24" aria-hidden="true"><path d="M2 5h20v14H2z M2 5l10 8 10-8" fill="none" stroke="#fff" stroke-width="2"/></svg>
          paul@velkpartners.example
        </li>
      </ul>
    </div>
  </section>
</main>
</body>
</html>
```